Help design website for "Brightwater Civic Advisors" to advance the common good

Here is the Google doc link that lays out the design:

https://files.plumrivet.example/sheet/d/7QmTzR2wLx9KpVbN4hJcY8sEaUoFdG3iXkMnPq5rWt6/edit?usp=sharing

Here is the Google drive folder with the logos and photos: https://vault.plumrivet.example/open?id=4HkWp9LzQe2TxRvN8mBaYc3DsUoJfG6

The testimonials are being gathered and will be shared by Friday, 1/4.

The winner will also have to migrate the coding files to my hosting site.

Thank you for your help! Looking forward to seeing your designs.

Target Market(s)

Prospective clients

Industry/Entity Type

Non Profit

Coding

Coded - Design and coding required

Number of Pages Required

5+ page

Requirements
Must have
• Noted in the Google doc regarding layout.
Nice to have

```html
<!DOCTYPE html>
<html lang="en">
<head>
<meta charset="utf-8">
<title>Contact Us · Brightwater Civic Advisors</title>
<link href="https://fonts.googleapis.com/css2?family=Montserrat:wght@400;500;600&display=swap" rel="stylesheet">
<style>
:root{
  --brand-blue:#4a9bd6;
  --ink:#2f3338;
  --muted:#6b6f74;
  --header-bg:#f6f6f6;
  --panel-bg:#f5f5f5;
  --field-border:#cfcfcf;
  --footer-bg:#2c3240;
  --white:#ffffff;
}
*{box-sizing:border-box;margin:0;padding:0}
html,body{width:1200px;height:964px;overflow:hidden;background:var(--white);font-family:"Montserrat",Arial,sans-serif;color:var(--ink)}
.page{position:relative;width:1200px;height:964px}

.site-header{position:absolute;left:0;top:0;width:1200px;height:103px;background:var(--header-bg);border-bottom:1px solid #ececec}
.brand{position:absolute;left:80px;top:34px;display:flex;align-items:center;gap:12px}
.brand-mark{width:34px;height:34px;background:var(--brand-blue)}
.brand-name{font-size:17px;font-weight:500;letter-spacing:2.5px;text-transform:uppercase;color:var(--ink)}
.main-nav a{position:absolute;top:46px;font-size:11px;font-weight:500;letter-spacing:1.2px;text-transform:uppercase;color:var(--ink);text-decoration:none}
.nav-about{left:529px}
.nav-services{left:628px}
.nav-media{left:831px}
.nav-contact{position:absolute;left:976px;top:36px;width:143px;height:32px;background:var(--brand-blue);color:var(--white);font-size:11px;font-weight:500;letter-spacing:1.2px;text-transform:uppercase;display:flex;align-items:center;justify-content:center;border-radius:2px}

.intro{position:absolute;left:0;top:168px;width:1200px;text-align:center}
.intro h1{font-size:24px;font-weight:500;color:var(--ink)}
.rates{width:660px;margin:16px auto 0;font-size:12px;line-height:18px;color:var(--muted)}
.rates strong{color:var(--brand-blue);font-weight:600}

.consult-panel{position:absolute;left:80px;top:327px;width:1039px;height:492px;background:var(--panel-bg)}
.consult-panel h2{position:absolute;top:61px;width:100%;text-align:center;font-size:15.5px;font-weight:500;color:var(--ink)}
.consult-lead{position:absolute;top:98px;left:0;width:100%;text-align:center;font-size:12px;line-height:18px;color:var(--muted)}
.field{position:absolute;background:var(--white);border:1px solid var(--field-border);border-radius:2px;font-size:12px;color:var(--muted);padding:0 14px;display:flex;align-items:center}
.field-name{left:160px;top:170px;width:351px;height:33px}
.field-org{left:528px;top:170px;width:351px;height:33px}
.field-email{left:160px;top:218px;width:351px;height:33px}
.field-subject{left:528px;top:218px;width:351px;height:33px}
.field-message{left:160px;top:269px;width:719px;height:93px;align-items:flex-start;padding-top:10px}
.submit{position:absolute;left:464px;top:380px;width:112px;height:33px;background:var(--brand-blue);color:var(--white);font-size:11px;font-weight:600;letter-spacing:1.3px;text-transform:uppercase;display:flex;align-items:center;justify-content:center;border-radius:2px}

.site-footer{position:absolute;left:0;top:901px;width:1200px;height:63px;background:var(--footer-bg);color:var(--white);font-size:12px}
.footer-mark{position:absolute;left:80px;top:16px;width:32px;height:32px;background:var(--brand-blue)}
.footer-item{position:absolute;top:24px;white-space:nowrap}
.footer-copy{left:161px}
.footer-phone{left:536px}
.footer-email{left:709px}
.footer-item .accent{color:var(--brand-blue)}
.back-to-top{position:absolute;left:1080px;top:0;width:39px;height:63px;background:var(--white);display:flex;align-items:center;justify-content:center}
</style>
</head>
<body>
<div class="page">
  <header class="site-header">
    <div class="brand">
      <span class="brand-mark"></span>
      <span class="brand-name">Brightwater Civic Advisors</span>
    </div>
    <nav class="main-nav">
      <a class="nav-about" href="#">About Us</a>
      <a class="nav-services" href="#">Services &amp; Testimonials</a>
      <a class="nav-media" href="#">Media &amp; Impact</a>
    </nav>
    <span class="nav-contact">Contact Us</span>
  </header>

  <section class="intro">
    <h1>Contact Us</h1>
    <p class="rates"><strong>Rates:</strong> Depending on the services requested, Nora offers an hourly rate, a package rate, or a retainer fee based on the scope and complexity of the project.</p>
  </section>

  <section class="consult-panel">
    <h2>Book a Complimentary Consultation</h2>
    <p class="consult-lead">Use the form below to tell Nora about your inquiry, and she will schedule a 30-minute meeting, phone call,<br>or video chat to discuss your project outcomes.</p>
    <div class="field field-name">Full Name</div>
    <div class="field field-org">Organization Name</div>
    <div class="field field-email">Email Address</div>
    <div class="field field-subject">Subject</div>
    <div class="field field-message">Message</div>
    <div class="submit">Submit</div>
  </section>

  <footer class="site-footer">
    <span class="footer-mark"></span>
    <span class="footer-item footer-copy">© 2019 <span class="accent">Brightwater Civic Advisors.</span>&nbsp; All Rights Reserved.</span>
    <span class="footer-item footer-phone"><span class="accent">Phone:</span> (555) 014-2870</span>
    <span class="footer-item footer-email"><span class="accent">Email:</span> nora@brightwatercivic.example</span>
    <span class="back-to-top">
      <svg width="12" height="14" viewBox="0 0 12 14" aria-hidden="true"><path d="M6 0 L12 14 L6 10 L0 14 Z" fill="#4a9bd6"/></svg>
    </span>
  </footer>
</div>
</body>
</html>
```